Book cover design for a collection of poetry - The Lanternfield

Book cover and back design need to be moody, nostalgic, reflective, ethereal. Melancholy and other worldly. Cover design should not be time specific to a period or place but if applicable should reflect British landscape. Book cover should be in tones of blue and must include the title and author (THE LANTERNFIELD BY CORBIN WHITLACE). We love the idea of rain, and looking out of a window. See attached designs. A world you are observing but not in.

Industry/Entity Type

Book Publisher

Font styles to use
Serif
Script

Colors
3176b5
3377b5
85acd3
eaf1f7
0792cd
33a6d7
86cae7
ecf7fb
86cfc6

Requirements
Must have
• The colour blue in it, must be melancholy and reflective.
Nice to have
• Rain in the cover.
Should not have
• Any bright colours.

```html
<!DOCTYPE html>
<html lang="en">
<head>
<meta charset="utf-8">
<title>The Lanternfield — Corbin Whitlace</title>
<link rel="stylesheet" href="https://fonts.googleapis.com/css2?family=Bodoni+Moda:opsz,wght@6..96,700&family=Dosis:wght@400;500&display=swap">
<style>
  :root {
    --sky-top: #3f6f7a;
    --sky-haze: #8fb2b4;
    --sky-mid: #4f8590;
    --ground-dark: #0c1513;
    --ground-mid: #16302f;
    --ink-light: #f3f6f6;
    --fold-line: rgba(220, 235, 236, 0.28);
  }
  * { margin: 0; padding: 0; box-sizing: border-box; }
  html, body { width: 1200px; height: 873px; overflow: hidden; background: var(--ground-dark); }
  .cover-wrap {
    position: relative;
    width: 1200px;
    height: 873px;
    overflow: hidden;
    color: var(--ink-light);
  }
  .rain-window-photo {
    position: absolute;
    inset: 0;
    background:
      radial-gradient(ellipse 420px 120px at 240px 300px, rgba(190, 200, 180, 0.35), transparent 70%),
      radial-gradient(ellipse 520px 90px at 700px 250px, rgba(160, 196, 196, 0.35), transparent 70%),
      linear-gradient(180deg,
        var(--sky-top) 0%,
        #4d8089 18%,
        var(--sky-haze) 30%,
        var(--sky-mid) 38%,
        #3a6c74 44%,
        var(--ground-mid) 52%,
        #0f1f1d 68%,
        var(--ground-dark) 100%);
  }
  .fold {
    position: absolute;
    top: 0;
    width: 1px;
    height: 873px;
    background: var(--fold-line);
  }
  .fold--left { left: 545px; }
  .fold--right { left: 655px; }

  .back-cover {
    position: absolute;
    left: 84px;
    top: 376px;
    width: 376px;
    font-family: "Dosis", sans-serif;
    font-weight: 500;
    font-size: 14.5px;
    line-height: 27.3px;
    letter-spacing: 0.02em;
    text-transform: uppercase;
    text-align: center;
  }
  .back-cover p + p { margin-top: 27px; }

  .spine-author {
    position: absolute;
    left: 545px;
    width: 110px;
    top: 104px;
    font-family: "Dosis", sans-serif;
    font-weight: 500;
    font-size: 19px;
    line-height: 29px;
    text-align: center;
    letter-spacing: 0.03em;
  }
  .spine-title {
    position: absolute;
    left: 578px;
    top: 262px;
    writing-mode: vertical-rl;
    font-family: "Bodoni Moda", serif;
    font-weight: 700;
    font-size: 37px;
    letter-spacing: 0.3em;
    line-height: 42px;
    white-space: nowrap;
  }

  .front-title {
    position: absolute;
    left: 656px;
    width: 544px;
    top: 474px;
    font-family: "Bodoni Moda", serif;
    font-weight: 700;
    font-size: 58px;
    line-height: 68px;
    text-align: center;
    letter-spacing: 0.14em;
  }
  .front-title span { display: block; }
  .front-author {
    position: absolute;
    left: 656px;
    width: 544px;
    top: 636px;
    font-family: "Dosis", sans-serif;
    font-weight: 400;
    font-size: 22px;
    letter-spacing: 0.38em;
    text-align: center;
    padding-left: 0.38em;
  }
</style>
</head>
<body>
<main class="cover-wrap">
  <div class="rain-window-photo" role="img" aria-label="Photograph through a rain-spattered window at dusk: blurred blue sky, hazy light, dark silhouettes of buildings and lamp posts"></div>
  <div class="fold fold--left"></div>
  <div class="fold fold--right"></div>

  <section class="back-cover">
    <p>The Lanternfield is a collection of poetry.</p>
    <p>Told in two parts we first meet Charles — aged, crippled and left alone in his inherited marsh house - reflecting on his life and his marriage to beautiful Alice who we meet in part two. Alice is suicidal, manically depressed and struggling with life as a wife and mother. She meets, harbors and falls in love with a soldier during WWII and her world is changed forever.</p>
    <p>Moving through the 20th century, this life and the next, The Lanternfield interweaves grief, loss, the after-life, mental illness, and ultimately the true nature of love.</p>
  </section>

  <div class="spine-author">Corbin<br>Whitlace</div>
  <div class="spine-title">The Lanternfield</div>

  <h1 class="front-title"><span>The</span><span>Lanternfield</span></h1>
  <p class="front-author">Corbin Whitlace</p>
</main>
</body>
</html>
```